Graphics for New Online Software

Looking at a designer to design a UI/UX Interface for an Online Events Platform (just JPEG) and some corresponding images for a website content (i.e. features etc)

Deliverables:
1x User Interface Design for the Platform (refer to attachment)
5-6x Feature Listing Images (refer to attachment)

Target Market(s)

Technology, Online Users Etc

Industry/Entity Type

Software Developer

Number of Pages Required

1 page

Font styles to use
Sans Serif

Colors
34a7d8
0493ce
3176b5
85acd3

Requirements
Must have
• Looks like a well built software - examples:
https://gravelmoor.io/
https://quintaro.com/

All the images should look very professional, as though you are using it on the online platform itself.
Nice to have
• Refer to attached "Feature Listing" and Logo

```html
<!DOCTYPE html>
<html lang="en">
<head>
<meta charset="utf-8">
<title>Venuelo – Online Events Platform UI</title>
<link href="https://fonts.googleapis.com/css2?family=Montserrat:wght@400;500;600;700;800&display=swap" rel="stylesheet">
<style>
:root{
  --stage-bg:#c6c6c6;
  --blue:#2340f0;
  --blue-deep:#1c2fd8;
  --sky:#35aaf9;
  --ink:#1b1b22;
  --muted:#555766;
  --main-bg:#efedf9;
  --white:#ffffff;
  --line:#d9dbe6;
  --avatar:#b89b86;
}
*{box-sizing:border-box;margin:0;padding:0}
html,body{width:1200px;height:944px;overflow:hidden}
body{background:var(--stage-bg);font-family:'Montserrat',sans-serif;color:var(--ink);position:relative}
.screen{position:absolute;width:547px;height:420px;background:var(--main-bg);overflow:hidden}
.screen--stage{left:40px;top:29px}
.screen--info{left:603px;top:29px}
.screen--breakouts{left:40px;top:472px}
.screen--rewards{left:603px;top:472px}

/* header */
.topbar{position:absolute;left:0;top:0;width:100%;height:42px;background:var(--white)}
.brand{position:absolute;left:14px;top:11px;font-size:16px;font-weight:800;color:var(--ink);letter-spacing:-.2px}
.search{position:absolute;left:181px;top:10px;width:146px;height:19px;border:1px solid #b9bccb;border-radius:10px;font-size:5px;color:#7a7d8c;display:flex;align-items:center;padding-left:8px;gap:3px}
.tool{position:absolute;top:12px}
.tool--bell{left:400px}
.tool--gear{left:431px}
.divider{position:absolute;top:13px;width:1px;height:14px;background:var(--line)}
.user{position:absolute;left:466px;top:10px;display:flex;align-items:center;gap:4px}
.avatar{width:15px;height:15px;border-radius:50%;background:var(--avatar);display:block}
.user small{display:block;font-size:4.5px;color:var(--blue)}
.user span{display:block;font-size:5.5px;color:var(--ink)}

/* sidebar */
.sidebar{position:absolute;left:0;top:42px;width:80px;height:378px;background:linear-gradient(180deg,var(--blue) 0%,#2b6ef7 55%,var(--sky) 100%)}
.nav{list-style:none;padding-top:2px}
.nav li{height:24px;display:flex;align-items:center;padding-left:10px;font-size:6px;font-weight:700;color:var(--white);position:relative;letter-spacing:.1px}
.nav li.is-active{background:var(--blue-deep)}
.nav li.is-active svg{position:absolute;right:4px;top:6px}

/* main */
.duration{position:absolute;right:25px;top:48px;font-size:5px;font-weight:600;color:var(--ink)}
.duration b{color:var(--blue);font-weight:600}
.footer{position:absolute;left:80px;right:0;bottom:0;height:26px;background:var(--white);font-size:5.5px;color:var(--muted);display:flex;align-items:center;justify-content:center}
.card{position:absolute;background:var(--white);box-shadow:0 1px 3px rgba(40,40,90,.08)}
.heading{font-size:9px;font-weight:700;color:var(--blue);letter-spacing:.2px}
.link{display:block;font-size:5px;font-weight:700;color:var(--blue)}

/* stage */
.video{position:absolute;left:101px;top:61px;width:290px;height:192px;background:linear-gradient(135deg,#6e6a66,#3b3e46 55%,#cfcdc8)}
.video svg{position:absolute;left:129px;top:80px}
.qa{left:400px;top:61px;width:125px;height:192px;padding:8px 10px}
.bubble{position:absolute;font-size:4px;line-height:1.5;padding:4px 5px;width:85px}
.bubble em{display:block;font-style:normal;font-weight:600;text-align:right}
.bubble--own{background:#2f8df5;color:var(--white)}
.bubble--reply{border:1px solid #4a73e8;color:var(--muted);background:var(--white)}
.chat-avatar{position:absolute;width:14px;height:14px;border-radius:50%;background:var(--avatar)}
.program{left:100px;top:260px;width:427px;height:117px;padding:19px 18px}
.program-cols{display:flex;gap:13px;margin-top:12px}
.program-cols div{width:88px}
.program-cols h4{font-size:6px;font-weight:700;line-height:1.4;margin-bottom:5px}
.program-cols p{font-size:4.6px;color:var(--muted);line-height:1.55;margin-bottom:6px}

/* info */
.agenda{left:101px;top:64px;width:208px;height:190px;padding:10px 16px}
.agenda-photo{width:180px;height:96px;margin:7px 0 0 -1px;background:linear-gradient(120deg,#6d8bb0,#b9c7d6 50%,#4e6583)}
.agenda h4{font-size:6.5px;font-weight:700;line-height:1.4;margin-top:13px}
.agenda p{font-size:6px;color:var(--muted);line-height:1.5;margin-top:2px}
.prog-list{left:318px;top:64px;width:208px;height:190px;padding:10px 15px}
.prog-item{padding:10px 0 9px;border-bottom:1px solid var(--line)}
.prog-item:first-of-type{padding-top:8px}
.prog-item:last-child{border-bottom:0}
.prog-item h4{font-size:6px;font-weight:700;margin-bottom:3px}
.prog-item p{font-size:4.6px;color:var(--muted);line-height:1.5;margin-bottom:4px}
.speakers{left:100px;top:260px;width:427px;height:122px;padding:13px 15px}
.speakers .pager{position:absolute;right:12px;top:12px}
.speaker-row{display:flex;margin-top:10px}
.speaker{flex:1;text-align:center;border-right:1px solid var(--line)}
.speaker:last-child{border-right:0}
.speaker .photo{display:block;width:43px;height:43px;border-radius:50%;background:linear-gradient(160deg,#c9d4dd,#8f7b6c);margin:0 auto 7px}
.speaker h5{font-size:6px;font-weight:700}
.speaker p{font-size:4.6px;color:var(--muted);line-height:1.5;margin-top:2px}

/* breakouts */
.room{width:202px;height:92px;padding:15px 21px}
.room h3{font-size:9.5px;font-weight:700;color:var(--blue)}
.room p{font-size:6.5px;color:var(--ink);margin-top:7px}
.room .btn{display:inline-block;margin-top:7px;border:1px solid var(--blue);padding:4px 8px;font-size:5.5px;font-weight:700;color:var(--blue)}

/* rewards */
.rewards{left:97px;top:61px;width:418px;height:310px}
.task{position:absolute;top:15px;width:126px;height:54px;border:1px solid var(--blue);display:flex;flex-direction:column;align-items:center;justify-content:center;gap:6px;font-size:7.5px;font-weight:700;color:var(--blue)}
.points{position:absolute;left:21px;top:92px;font-size:13px;font-weight:700;color:var(--blue)}
.collect{position:absolute;left:20px;top:118px;font-size:11px;font-weight:700;color:var(--ink)}
.note{position:absolute;left:21px;font-size:7px;color:var(--ink)}
.note u{text-decoration:underline}
</style>
</head>
<body>

<svg width="0" height="0" style="position:absolute">
  <defs>
    <symbol id="ico-chevrons" viewBox="0 0 12 12"><path d="M2 1l4 5-4 5M6 1l4 5-4 5" fill="none" stroke="#5cc2ff" stroke-width="2"/></symbol>
    <symbol id="ico-search" viewBox="0 0 10 10"><circle cx="4" cy="4" r="3" fill="none" stroke="#2340f0" stroke-width="1.5"/><path d="M6.3 6.3L9 9" stroke="#2340f0" stroke-width="1.5"/></symbol>
    <symbol id="ico-bell" viewBox="0 0 12 12"><path d="M6 1a3.5 3.5 0 0 0-3.5 3.5V8L1.5 9.5h9L9.5 8V4.5A3.5 3.5 0 0 0 6 1z" fill="#2340f0"/><circle cx="6" cy="10.8" r="1.1" fill="#2340f0"/></symbol>
    <symbol id="ico-gear" viewBox="0 0 12 12"><circle cx="6" cy="6" r="3.4" fill="none" stroke="#2340f0" stroke-width="2"/><path d="M6 0v2.5M6 9.5V12M0 6h2.5M9.5 6H12M1.8 1.8l1.8 1.8M8.4 8.4l1.8 1.8M1.8 10.2l1.8-1.8M8.4 3.6l1.8-1.8" stroke="#2340f0" stroke-width="1.8"/></symbol>
    <symbol id="ico-check" viewBox="0 0 12 12"><circle cx="6" cy="6" r="6" fill="#2f8df5"/><path d="M3.2 6.2l2 2 3.8-4" fill="none" stroke="#fff" stroke-width="1.5"/></symbol>
  </defs>
</svg>

<!-- Stage -->
<section class="screen screen--stage">
  <header class="topbar">
    <div class="brand">VENUELO</div>
    <div class="search"><svg width="6" height="6"><use href="#ico-search"/></svg>Enter Keyword</div>
    <svg class="tool tool--bell" width="10" height="10"><use href="#ico-bell"/></svg>
    <span class="divider" style="left:419px"></span>
    <svg class="tool tool--gear" width="10" height="10"><use href="#ico-gear"/></svg>
    <span class="divider" style="left:452px"></span>
    <div class="user"><span class="avatar" role="img" aria-label="User avatar"></span><div><small>Welcome</small><span>Author Name</span></div></div>
  </header>
  <nav class="sidebar"><ul class="nav">
    <li>EVENT INFO</li><li class="is-active">STAGE<svg width="12" height="12"><use href="#ico-chevrons"/></svg></li><li>BREAKOUTS</li><li>BOOTHS</li><li>VIRTUAL EXHIBITION</li><li>REWARDS</li>
  </ul></nav>
  <p class="duration"><b>Event Duration</b> (Remaining 05:25)</p>
  <div class="video" role="img" aria-label="Live stage video of a presenter working at a laptop">
    <svg width="32" height="32" viewBox="0 0 32 32"><circle cx="16" cy="16" r="14" fill="none" stroke="#fff" stroke-width="2"/><path d="M12.5 9.5l10 6.5-10 6.5z" fill="#fff"/></svg>
  </div>
  <div class="card qa">
    <h2 class="heading">Q&amp;A CHAT</h2>
    <span class="chat-avatar" style="left:9px;top:26px" role="img" aria-label="Attendee avatar"></span>
    <div class="bubble bubble--own" style="left:29px;top:25px">Augiat in pede Fusce tellus Sed metus augue convallis et vehi<em style="text-align:left">By Author Name</em></div>
    <div class="bubble bubble--reply" style="left:9px;top:62px">Augiat in pede Fusce tellus Sed metus augue convallis et vehi<em>By Author Name</em></div>
    <span class="chat-avatar" style="left:100px;top:63px" role="img" aria-label="Attendee avatar"></span>
    <span class="chat-avatar" style="left:8px;top:99px" role="img" aria-label="Attendee avatar"></span>
    <div class="bubble bubble--reply" style="left:28px;top:98px">Augiat in pede Fusce tellus Sed metus augue convallis et vehicula ut pulvinar eu ante Integer orci tellus tristique vitae consequat<em style="text-align:left">By Author Name</em></div>
    <div class="bubble bubble--reply" style="left:9px;top:146px">Augiat in pede Fusce tellus Sed metus augue convallis et vehi<em>By Author Name</em></div>
    <span class="chat-avatar" style="left:100px;top:147px" role="img" aria-label="Attendee avatar"></span>
  </div>
  <div class="card program">
    <h2 class="heading">PROGRAMMING</h2>
    <div class="program-cols">
      <div><h4>Curabitur vel mi sit amet magna malesuada</h4><p>Curabitur vel dolor ultrices ipsum dictum tristique Praesent vitae lacus Ut velit enim vestib</p><span class="link">LEARN MORE ›</span></div>
      <div><h4>Augiat in pede Fusce tellus Sed metus</h4><p>Curabitur vel dolor ultrices ipsum dictum tristique Praesent vitae lacus Ut velit enim vestib</p><span class="link">LEARN MORE ›</span></div>
      <div><h4>Nunc tempus felis vitae urna Vivamus</h4><p>Curabitur vel dolor ultrices ipsum dictum tristique Praesent vitae lacus Ut velit enim vestib</p><span class="link">LEARN MORE ›</span></div>
      <div><h4>Vivamus porttitor neque at volutpat rutrum</h4><p>Curabitur vel dolor ultrices ipsum dictum tristique Praesent vitae lacus Ut velit enim vestib</p><span class="link">LEARN MORE ›</span></div>
    </div>
  </div>
  <footer class="footer">© 2020 Company Name | All Rights Reserved</footer>
</section>

<!-- Event info -->
<section class="screen screen--info">
  <header class="topbar">
    <div class="brand">VENUELO</div>
    <div class="search" style="left:184px;top:13px"><svg width="6" height="6"><use href="#ico-search"/></svg>Enter Keyword</div>
    <svg class="tool tool--bell" style="top:15px" width="10" height="10"><use href="#ico-bell"/></svg>
    <span class="divider" style="left:419px;top:16px"></span>
    <svg class="tool tool--gear" style="top:15px" width="10" height="10"><use href="#ico-gear"/></svg>
    <span class="divider" style="left:452px;top:16px"></span>
    <div class="user" style="top:14px"><span class="avatar" role="img" aria-label="User avatar"></span><div><small>Welcome</small><span>Author Name</span></div></div>
  </header>
  <nav class="sidebar"><ul class="nav" style="padding-top:0">
    <li class="is-active">EVENT INFO<svg width="12" height="12"><use href="#ico-chevrons"/></svg></li><li>STAGE</li><li>BREAKOUTS</li><li>BOOTHS</li><li>VIRTUAL EXHIBITION</li><li>REWARDS</li>
  </ul></nav>
  <p class="duration" style="right:21px"><b>Event Duration</b> (Remaining 05:25)</p>
  <div class="card agenda">
    <h2 class="heading">AGENDA</h2>
    <div class="agenda-photo" role="img" aria-label="Team meeting around a conference table"></div>
    <h4>Augiat in pede Fusce tellus Sed metus augue convallis et vehicula ut pulvinar</h4>
    <p>ante Integer orci tellus tristique vitae consequat nec mauris viverra in gravida eu mattis in ante Mo</p>
  </div>
  <div class="card prog-list">
    <h2 class="heading">PROGRAMMING</h2>
    <div class="prog-item"><h4>Curabitur vel mi sit amet magna</h4><p>Curabitur vel dolor ultrices ipsum dictum tristique Praesent vitae lacus Ut velit enim vestib</p><span class="link">CLICK HERE ›</span></div>
    <div class="prog-item"><h4>Ait amet magna malesuada</h4><p>Curabitur vel dolor ultrices ipsum dictum tristique Praesent vitae lacus Ut velit enim vestib</p><span class="link">CLICK HERE ›</span></div>
    <div class="prog-item"><h4>Curabitur vel mi sit amet magna</h4><p>Curabitur vel dolor ultrices ipsum dictum tristique Praesent vitae lacus Ut velit enim vestib</p><span class="link">CLICK HERE ›</span></div>
  </div>
  <div class="card speakers">
    <h2 class="heading">SPEAKERS</h2>
    <svg class="pager" width="22" height="8" viewBox="0 0 22 8"><path d="M4 1L1 4l3 3" fill="none" stroke="#c7c9d6" stroke-width="1.2"/><path d="M16 1l3 3-3 3" fill="none" stroke="#2340f0" stroke-width="1.4"/></svg>
    <div class="speaker-row">
      <div class="speaker"><span class="photo" role="img" aria-label="Speaker portrait"></span><h5>Speaker Name</h5><p>Curabitur vel dolor ultrices<br>ipsum dictum tristique</p></div>
      <div class="speaker"><span class="photo" role="img" aria-label="Speaker portrait"></span><h5>Speaker Name</h5><p>Curabitur vel dolor ultrices<br>ipsum dictum tristique</p></div>
      <div class="speaker"><span class="photo" role="img" aria-label="Speaker portrait"></span><h5>Speaker Name</h5><p>Curabitur vel dolor ultrices<br>ipsum dictum tristique</p></div>
      <div class="speaker"><span class="photo" role="img" aria-label="Speaker portrait"></span><h5>Speaker Name</h5><p>Curabitur vel dolor ultrices<br>ipsum dictum tristique</p></div>
      <div class="speaker"><span class="photo" role="img" aria-label="Speaker portrait"></span><h5>Speaker Name</h5><p>Curabitur vel dolor ultrices<br>ipsum dictum tristique</p></div>
    </div>
  </div>
  <footer class="footer">© 2020 Company Name | All Rights Reserved</footer>
</section>

<!-- Breakouts -->
<section class="screen screen--breakouts">
  <header class="topbar">
    <div class="brand">VENUELO</div>
    <div class="search" style="left:176px;top:12px"><svg width="6" height="6"><use href="#ico-search"/></svg>Enter Keyword</div>
    <svg class="tool tool--bell" style="left:395px;top:14px" width="10" height="10"><use href="#ico-bell"/></svg>
    <span class="divider" style="left:414px;top:15px"></span>
    <svg class="tool tool--gear" style="left:426px;top:14px" width="10" height="10"><use href="#ico-gear"/></svg>
    <span class="divider" style="left:447px;top:15px"></span>
    <div class="user" style="left:458px;top:13px"><span class="avatar" role="img" aria-label="User avatar"></span><div><small>Welcome</small><span>Author Name</span></div></div>
  </header>
  <nav class="sidebar"><ul class="nav">
    <li>EVENT INFO</li><li>STAGE</li><li class="is-active">BREAKOUTS<svg width="12" height="12"><use href="#ico-chevrons"/></svg></li><li>BOOTHS</li><li>VIRTUAL EXHIBITION</li><li>REWARDS</li>
  </ul></nav>
  <p class="duration" style="right:40px"><b>Event Duration</b> (Remaining 05:25)</p>
  <div class="card room" style="left:97px;top:65px"><h3>JOIN BREAKOUT ROOM 1</h3><p>(4/50)</p><p>3.00PM TO 4.30PM</p><span class="btn">3RD PARTY MEETLY ROOM</span></div>
  <div class="card room" style="left:308px;top:65px"><h3>JOIN BREAKOUT ROOM 2</h3><p>(10/50)</p><p>3.00PM TO 4.30PM</p><span class="btn">3RD PARTY MEETLY ROOM</span></div>
  <div class="card room" style="left:97px;top:166px"><h3>JOIN BREAKOUT ROOM 3</h3><p>(4/50)</p><p>3.00PM TO 4.30PM</p><span class="btn">3RD PARTY MEETLY ROOM</span></div>
  <div class="card room" style="left:308px;top:166px"><h3>JOIN BREAKOUT ROOM 4</h3><p>(10/50)</p><p>3.00PM TO 4.30PM</p><span class="btn">3RD PARTY MEETLY ROOM</span></div>
  <footer class="footer">© 2020 Company Name | All Rights Reserved</footer>
</section>

<!-- Rewards -->
<section class="screen screen--rewards">
  <header class="topbar">
    <div class="brand">VENUELO</div>
    <div class="search" style="left:176px;top:12px"><svg width="6" height="6"><use href="#ico-search"/></svg>Enter Keyword</div>
    <svg class="tool tool--bell" style="left:395px;top:14px" width="10" height="10"><use href="#ico-bell"/></svg>
    <span class="divider" style="left:414px;top:15px"></span>
    <svg class="tool tool--gear" style="left:426px;top:14px" width="10" height="10"><use href="#ico-gear"/></svg>
    <span class="divider" style="left:447px;top:15px"></span>
    <div class="user" style="left:458px;top:13px"><span class="avatar" role="img" aria-label="User avatar"></span><div><small>Welcome</small><span>Author Name</span></div></div>
  </header>
  <nav class="sidebar"><ul class="nav">
    <li>EVENT INFO</li><li>STAGE</li><li>BREAKOUTS</li><li>BOOTHS</li><li>VIRTUAL EXHIBITION</li><li class="is-active">REWARDS<svg width="12" height="12"><use href="#ico-chevrons"/></svg></li>
  </ul></nav>
  <p class="duration" style="right:34px;top:47px"><b>Event Duration</b> (Remaining 05:25)</p>
  <div class="card rewards">
    <div class="task" style="left:18px"><svg width="12" height="12"><use href="#ico-check"/></svg>Visited Virtual Exhibition</div>
    <div class="task" style="left:148px"><svg width="12" height="12"><use href="#ico-check"/></svg>Joined Breakout Room</div>
    <div class="task" style="left:278px"><svg width="12" height="12"><use href="#ico-check"/></svg>Checked out Booths</div>
    <p class="points">Total Points: 40</p>
    <p class="collect">Collect Reward - Trigger Email/Link to 3rd Party App</p>
    <p class="note" style="top:142px">Flash them a PROMO CODE/“Email will be given to you on how you can claim your prize)</p>
    <p class="note" style="top:158px">- they can go to <u>www.prizeloop.com</u> to claim</p>
  </div>
  <footer class="footer">© 2020 Company Name | All Rights Reserved</footer>
</section>

</body>
</html>
```